project - Misto Den

Dear designers, I'm Looking for an appealing new business card design to represent us for our new e-cigarette store: The MistO Den. Knowledgeable and friendly staff we aim for superior customer service with a positive atmosphere. Classic feel with modern touch is what we are aiming for . Lime green font and grey back round is the original color scheme but we are flexible and open to suggestions. I added some doodles to show you where my mind is at. address: 4827 203 St SW Edmonton, AB (inside the grand swap bazaar)web: themistoden.com email: info@themistoden.com phone : 555.214.6093 Thanks and am looking forward to seeing your creative , fresh and innovative designs.
Good luck everybody!
Gordon
Updates
lime green and charcoal grey please. thanks
Industry/Entity Type
Business
Logo Text
The MistO Den
Look and feel
Each slider illustrates characteristics of the customer's brand and the style your logo design should communicate.

```html
<!DOCTYPE html>
<html lang="en">
<head>
<meta charset="utf-8">
<title>Misto Den — Business Card</title>
<link rel="stylesheet" href="https://fonts.googleapis.com/css2?family=Michroma&display=swap">
<style>
  :root {
    --page-bg: #e9eaea;
    --card-top: #ffffff;
    --card-top-shade: #dcdedf;
    --charcoal: #4a4b4d;
    --band-dark: #1f2021;
    --band-silver: #b9bcbe;
    --lime: #6cc04a;
    --lime-deep: #1f9a3c;
    --text-light: #ffffff;
  }
  * { box-sizing: border-box; margin: 0; padding: 0; }
  html, body { width: 1200px; height: 899px; overflow: hidden; }
  body {
    background: var(--page-bg);
    font-family: "Michroma", sans-serif;
    position: relative;
  }
  .card {
    position: absolute;
    left: 180px; top: 210px;
    width: 840px; height: 480px;
    border-radius: 44px;
    overflow: hidden;
    background: linear-gradient(180deg, var(--card-top) 0%, var(--card-top-shade) 45%);
    box-shadow: 0 12px 30px rgba(0,0,0,0.18);
  }
  .card-wave { position: absolute; inset: 0; width: 840px; height: 480px; }
  .brand-name {
    position: absolute;
    left: 78px; top: 78px;
    font-family: "Michroma", sans-serif;
    font-size: 70px;
    letter-spacing: -1px;
    color: var(--charcoal);
    line-height: 1;
    white-space: nowrap;
  }
  .holder {
    position: absolute;
    right: 470px; top: 268px;
    text-align: right;
    color: var(--text-light);
    font-size: 15px;
    line-height: 27px;
    letter-spacing: 1.5px;
    text-transform: uppercase;
    white-space: nowrap;
  }
  .holder .holder-name { font-size: 17px; }
  .divider {
    position: absolute;
    left: 388px; top: 262px;
    width: 2px; height: 150px;
    background: var(--text-light);
  }
  .contacts {
    position: absolute;
    left: 404px; top: 264px;
    list-style: none;
    color: var(--text-light);
    font-size: 14px;
    letter-spacing: 1.5px;
    line-height: 27px;
    white-space: nowrap;
  }
  .contacts li { display: flex; align-items: center; gap: 9px; }
  .contact-icon { width: 16px; height: 16px; flex: none; }
</style>
</head>
<body>
  <div class="card">
    <svg class="card-wave" viewBox="0 0 840 480" aria-hidden="true">
      <defs>
        <linearGradient id="limeFill" x1="0" y1="0" x2="0.4" y2="1">
          <stop offset="0" stop-color="#8fd25f"/>
          <stop offset="0.45" stop-color="#4fb046"/>
          <stop offset="1" stop-color="#1f9a3c"/>
        </linearGradient>
      </defs>
      <path d="M0,168 C240,150 480,232 840,186 L840,480 L0,480 Z" fill="var(--band-dark)"/>
      <path d="M0,184 C240,166 480,248 840,202 L840,480 L0,480 Z" fill="var(--band-silver)"/>
      <path d="M0,196 C240,178 480,260 840,214 L840,480 L0,480 Z" fill="url(#limeFill)"/>
    </svg>

    <div class="brand-name">MISTO DEN</div>

    <div class="holder">
      <p class="holder-name">Alan Brooks</p>
      <p>Owner / C.E.O</p>
      <p>Unit # 118, Park Blk,</p>
      <p>AB 40712</p>
    </div>

    <div class="divider"></div>

    <ul class="contacts">
      <li>
        <svg class="contact-icon" viewBox="0 0 16 16"><circle cx="8" cy="8" r="8" fill="#fff"/><path d="M5 4.5l1.6-.3.9 2-1 .8a5 5 0 0 0 2.5 2.5l.8-1 2 .9-.3 1.6c-3.4.3-6.8-3.1-6.5-6.5z" fill="var(--lime-deep)"/></svg>
        555.214.6093
      </li>
      <li>
        <svg class="contact-icon" viewBox="0 0 16 16"><circle cx="8" cy="8" r="8" fill="#fff"/><rect x="4.5" y="6" width="7" height="5" rx="0.8" fill="var(--lime-deep)"/><rect x="6" y="4" width="4" height="2.5" fill="var(--lime-deep)"/></svg>
        555.214.6094
      </li>
      <li>
        <svg class="contact-icon" viewBox="0 0 16 16"><circle cx="8" cy="8" r="8" fill="#fff"/><rect x="5.5" y="3.5" width="5" height="9" rx="1" fill="var(--lime-deep)"/><rect x="6.5" y="5" width="3" height="5" fill="#fff"/></svg>
        555.214.6095
      </li>
      <li>
        <svg class="contact-icon" viewBox="0 0 16 16"><circle cx="8" cy="8" r="8" fill="#fff"/><rect x="4" y="5" width="8" height="6" rx="0.8" fill="var(--lime-deep)"/><path d="M4.3 5.4L8 8.3l3.7-2.9" stroke="#fff" stroke-width="0.9" fill="none"/></svg>
        info@themistoden.com
      </li>
      <li>
        <svg class="contact-icon" viewBox="0 0 16 16"><circle cx="8" cy="8" r="8" fill="#fff"/><circle cx="8" cy="8" r="4.2" fill="none" stroke="var(--lime-deep)" stroke-width="1"/><path d="M3.8 8h8.4M8 3.8c-2 2.4-2 6 0 8.4M8 3.8c2 2.4 2 6 0 8.4" stroke="var(--lime-deep)" stroke-width="0.9" fill="none"/></svg>
        www.themistoden.com
      </li>
    </ul>
  </div>
</body>
</html>
```